Birchline Septic Solutions

Would like to see some single sided ones but would also like to see some double sided with one sided only being the logo. Owners name is Colin Vandro. Phone number is 555-214-0387
Services are pumping, inspections, installs, and repairs

Contact Information for Business Card

555-241-0387 Colin Vandro Greenfield, OH

```html
<!DOCTYPE html>
<html lang="en">
<head>
<meta charset="UTF-8">
<title>Birchline Septic Solutions – Business Cards</title>
<link href="https://fonts.googleapis.com/css2?family=Montserrat:wght@400;500;700&display=swap" rel="stylesheet">
<style>
  :root {
    --backdrop: #e3e3e1;
    --card: #ffffff;
    --teal: #2ebdb5;
    --ink: #1b1b1b;
    --muted: #2a2a2a;
    --emboss: #d6d6d6;
  }
  * { margin: 0; padding: 0; box-sizing: border-box; }
  html, body {
    width: 1200px; height: 801px; overflow: hidden;
    background: var(--backdrop);
    font-family: "Montserrat", Arial, sans-serif;
  }
  .stage {
    position: relative; width: 1200px; height: 801px;
    display: flex; align-items: center; justify-content: center; gap: 30px;
  }
  .card {
    position: relative; width: 540px; height: 309px;
    background: var(--card);
    border-bottom: 3px solid var(--teal);
    box-shadow: 0 6px 18px rgba(0,0,0,0.12);
    overflow: hidden;
  }

  /* Front */
  .brand-block {
    position: absolute; left: 24px; top: 60px; width: 256px; height: 140px;
    display: flex; flex-direction: column; align-items: center; justify-content: center;
  }
  .brand-name {
    font-weight: 700; color: var(--ink); text-align: center;
    font-size: 30px; line-height: 1.05; letter-spacing: 0.5px;
  }
  .brand-name .sub { display: block; font-size: 14px; letter-spacing: 4px; margin-top: 8px; }
  .brand-mark { width: 14px; height: 14px; background: var(--teal); margin-bottom: 12px; }

  .divider {
    position: absolute; left: 296px; top: 36px; width: 1.5px; height: 170px;
    background: var(--teal);
  }
  .contact { position: absolute; left: 318px; top: 36px; }
  .contact .name { color: var(--teal); font-weight: 700; font-size: 24px; line-height: 1; }
  .contact .role { color: var(--muted); font-size: 12px; margin-top: 4px; }
  .contact ul { list-style: none; margin-top: 18px; }
  .contact li {
    display: flex; align-items: center; gap: 7px;
    font-size: 13px; color: var(--muted); line-height: 1.55;
  }
  .contact li svg { width: 11px; height: 11px; flex: none; }
  .contact .address { margin-top: 12px; font-size: 13px; color: var(--muted); line-height: 1.4; }

  .services-band {
    position: absolute; left: 0; right: 0; top: 238px; height: 30px;
    background: var(--teal); color: #fff;
    display: flex; align-items: center; padding-left: 22px;
    font-size: 15px; font-weight: 500;
  }

  /* Back */
  .back {
    display: flex; flex-direction: column; align-items: center; justify-content: center;
  }
  .back .brand-name { color: var(--emboss); font-size: 58px; }
  .back .brand-name .sub { font-size: 22px; letter-spacing: 7px; margin-top: 14px; }
</style>
</head>
<body>
<main class="stage">
  <section class="card front" aria-label="Card front">
    <div class="brand-block">
      <span class="brand-mark"></span>
      <div class="brand-name">BIRCHLINE<span class="sub">SEPTIC SOLUTIONS</span></div>
    </div>

    <div class="divider"></div>

    <div class="contact">
      <div class="name">Colin Vandro</div>
      <div class="role">Owner</div>
      <ul>
        <li>
          <svg viewBox="0 0 24 24" fill="var(--teal)"><path d="M6.6 10.8a15.1 15.1 0 0 0 6.6 6.6l2.2-2.2a1 1 0 0 1 1-.25 11.4 11.4 0 0 0 3.6.57 1 1 0 0 1 1 1V20a1 1 0 0 1-1 1A17 17 0 0 1 3 4a1 1 0 0 1 1-1h3.5a1 1 0 0 1 1 1c0 1.25.2 2.45.57 3.57a1 1 0 0 1-.25 1z"/></svg>
          555-214-0387
        </li>
        <li>
          <svg viewBox="0 0 24 24" fill="var(--teal)"><path d="M2 5h20v14H2z"/><path d="M2 5l10 8 10-8" stroke="#fff" stroke-width="2" fill="none"/></svg>
          info@birchlineseptic.com
        </li>
        <li>
          <svg viewBox="0 0 24 24" fill="none" stroke="var(--teal)" stroke-width="2.4"><circle cx="12" cy="12" r="10"/><path d="M2 12h20M12 2c3 3 3 17 0 20M12 2c-3 3-3 17 0 20"/></svg>
          www.birchlineseptic.com
        </li>
      </ul>
      <p class="address">Your address, City<br>State, Zip 1234</p>
    </div>

    <div class="services-band">Services are pumping, inspections, installs, and repairs</div>
  </section>

  <section class="card back" aria-label="Card back">
    <div class="brand-name">BIRCHLINE<span class="sub">SEPTIC SOLUTIONS</span></div>
  </section>
</main>
</body>
</html>
```